Business Cards for a law firm

Business cards for our law firm. Use our silhoette logo and OAK PARTNERS - check our website (www.oakpartners.example)

Contact Information for Business Card

our silhouette logo, OAK PARTNERS, 800-555-0147, Dorian Pemberton, dorian@oakpartners.example

Requirements
Must have
• our silhouette logo, OAK PARTNERS, 800-555-0147, Dorian Pemberton, dorian@oakpartners.example

```html
<!DOCTYPE html>
<html lang="en">
<head>
<meta charset="utf-8">
<title>Oak Partners business card</title>
<link rel="stylesheet" href="https://fonts.googleapis.com/css2?family=Michroma&family=Poppins:wght@400;500&display=swap">
<style>
  :root {
    --navy: #1a3169;
    --ink: #1e1e24;
    --paper: #ffffff;
    --backdrop: #e9eaec;
  }
  * { box-sizing: border-box; margin: 0; padding: 0; }
  html, body { width: 1093px; height: 1200px; overflow: hidden; }
  body { background: var(--backdrop); position: relative; font-family: "Poppins", sans-serif; }

  .card {
    position: absolute;
    left: 258px;
    width: 578px;
    height: 356px;
    border-radius: 28px;
    overflow: hidden;
  }
  .card--front { top: 226px; background: var(--paper); }
  .card--back { top: 621px; background: var(--navy); }

  .brand {
    position: absolute;
    display: flex;
    align-items: center;
    gap: 12px;
    font-family: "Michroma", sans-serif;
    letter-spacing: 0.06em;
    white-space: nowrap;
  }
  .brand__mark { flex: none; }
  .card--front .brand { right: 32px; top: 72px; font-size: 20px; color: var(--navy); }
  .card--front .brand__mark { width: 20px; height: 20px; background: var(--navy); }
  .card--back .brand {
    left: 50%; top: 50%; transform: translate(-50%, -50%);
    font-size: 27px; color: var(--paper); gap: 16px;
  }
  .card--back .brand__mark { width: 26px; height: 26px; background: var(--paper); }

  .holder {
    position: absolute; left: 27px; top: 202px;
    font-family: "Michroma", sans-serif; font-size: 17px;
    color: var(--navy); letter-spacing: 0.01em; text-transform: uppercase;
  }
  .rule {
    position: absolute; left: 27px; top: 239px; width: 519px; height: 1px;
    background: var(--navy);
  }
  .contact { position: absolute; left: 27px; display: flex; align-items: center; gap: 6px; }
  .contact svg { flex: none; }
  .contact--phone { top: 258px; font-size: 23px; font-weight: 500; color: var(--navy); }
  .contact--email { top: 286px; font-size: 16px; color: var(--ink); }
  .website {
    position: absolute; right: 32px; top: 290px;
    font-size: 16px; color: var(--ink);
  }
  .website__domain { color: var(--navy); }
  .band { position: absolute; left: 0; right: 0; bottom: 0; height: 16px; background: var(--navy); }
</style>
</head>
<body>
  <section class="card card--front" aria-label="Card front">
    <div class="brand"><span class="brand__mark"></span><span class="brand__name">OAK PARTNERS</span></div>
    <h1 class="holder">Dorian Pemberton</h1>
    <div class="rule"></div>
    <div class="contact contact--phone">
      <svg width="25" height="25" viewBox="0 0 25 25" aria-hidden="true">
        <circle cx="12.5" cy="12.5" r="11.5" fill="none" stroke="#1a3169" stroke-width="1.3"/>
        <path d="M8.6 7.4l1.8-.6 1.2 2.6-1.2.9c.6 1.4 1.6 2.5 3 3.2l1-1.1 2.5 1.3-.6 1.8c-3.8.1-7.7-3.8-7.7-8.1z" fill="#1a3169"/>
      </svg>
      <span>800-555-0147</span>
    </div>
    <div class="contact contact--email">
      <svg width="25" height="25" viewBox="0 0 25 25" aria-hidden="true">
        <circle cx="12.5" cy="12.5" r="11.5" fill="none" stroke="#1a3169" stroke-width="1.3"/>
        <rect x="7" y="9" width="11" height="7.5" fill="#1a3169"/>
        <path d="M7 9l5.5 4.2L18 9" fill="none" stroke="#fff" stroke-width="0.9"/>
      </svg>
      <span>dorian@oakpartners.example</span>
    </div>
    <div class="website">www.<span class="website__domain">oakpartners</span>.example</div>
    <div class="band"></div>
  </section>

  <section class="card card--back" aria-label="Card back">
    <div class="brand"><span class="brand__mark"></span><span class="brand__name">OAK PARTNERS</span></div>
  </section>
</body>
</html>
```